Red Mo's Wine Label Project

We need a new entry level wine label called "Red Mo's" for a range of wines we are developing from inland Australia. Our company is made up of three youngish guys who live hard and love taking the mickey. Red Mo is Red Morrie - the largest and loudest of the three partners (and ideally this label will take the mickey out of him). We've grown the grapes ourselves for this first release which will be a 2012 Pinot Gris. Wine style is dry, young, fresh and contemporary and pitched at the sub AUD $10 retail price point. The package will be flint (clear) claret shape bottle with plain screwcap (colour matched to suit the winning label design).

I've attached a couple of photos of Red Morrie to give you some idea of his presence and persona.

Target Market(s)

Semi educated 25 - 40 year old wine drinkers. Skewed towards females.

Industry/Entity Type

Retail

Requirements
Should not have
• Anything traditional or old fashioned

```html
<!DOCTYPE html>
<html lang="en">
<head>
<meta charset="utf-8">
<title>Red Mo's – Pinot Gris 2012 Labels</title>
<link rel="stylesheet" href="https://fonts.googleapis.com/css2?family=Anton&family=Quicksand:wght@400;500&display=swap">
<style>
  :root {
    --page-bg: #f3f3f3;
    --label-white: #ffffff;
    --ink: #151515;
    --type-light: #ffffff;
    --green-field: #86bd79;
    --green-art: #2f6b36;
    --pink-field: #b92a5e;
    --pink-art: #3a1a22;
  }
  * { box-sizing: border-box; margin: 0; padding: 0; }
  html, body {
    width: 1037px;
    height: 1200px;
    overflow: hidden;
    background: var(--page-bg);
  }
  .label-range {
    width: 1037px;
    height: 1200px;
    display: flex;
    justify-content: center;
    align-items: center;
    gap: 120px;
  }
  .label {
    width: 320px;
    height: 980px;
    display: flex;
    flex-direction: column;
    box-shadow: 0 2px 10px rgba(0,0,0,0.08);
  }
  .label__brand {
    height: 290px;
    background: var(--label-white);
    display: flex;
    align-items: center;
    justify-content: center;
  }
  .label__brand-name {
    font-family: "Anton", sans-serif;
    font-size: 92px;
    line-height: 1;
    color: var(--ink);
    letter-spacing: 1px;
  }
  .label__field {
    flex: 1;
    display: flex;
    flex-direction: column;
    align-items: center;
    padding-top: 104px;
    color: var(--type-light);
    font-family: "Quicksand", sans-serif;
  }
  .label--white-wine .label__field { background: var(--green-field); }
  .label--red-wine .label__field { background: var(--pink-field); }
  .label__art {
    width: 236px;
    height: 344px;
    border-radius: 6px;
  }
  .label--white-wine .label__art { background: var(--green-art); opacity: 0.55; }
  .label--red-wine .label__art { background: var(--pink-art); opacity: 0.45; }
  .label__variety,
  .label__alcohol {
    font-size: 31px;
    font-weight: 500;
    line-height: 1.35;
    letter-spacing: 0.5px;
  }
  .label__variety { margin-top: 36px; }
  .label__vintage {
    font-size: 88px;
    font-weight: 400;
    line-height: 1;
    margin-top: 6px;
  }
</style>
</head>
<body>
  <main class="label-range">
    <section class="label label--white-wine">
      <header class="label__brand">
        <span class="label__brand-name">RED MO</span>
      </header>
      <div class="label__field">
        <div class="label__art" role="img" aria-label="Engraved illustration of a traditional wine press"></div>
        <p class="label__variety">PINOT GRIS</p>
        <p class="label__alcohol">ALKOHOL 12%</p>
        <p class="label__vintage">2012</p>
      </div>
    </section>

    <section class="label label--red-wine">
      <header class="label__brand">
        <span class="label__brand-name">RED MO</span>
      </header>
      <div class="label__field">
        <div class="label__art" role="img" aria-label="Engraved illustration of a T-handle corkscrew"></div>
        <p class="label__variety">PINOT GRIS</p>
        <p class="label__alcohol">ALKOHOL 12%</p>
        <p class="label__vintage">2012</p>
      </div>
    </section>
  </main>
</body>
</html>
```